creating a certificate for our flagship course

Hi,
We need a new certificate for our flagship course called Silver Harbour. We have been running this course for 25 years this year and want to get something special that represents that. We need our logos incorporated and we love to have a compass or Koru incorporated in the certificate. We like something different from your standard certificate, but not too crazy.

The text should say something along the lines of:
This certificate is awarded to ....
For successfully completing and contributing to the three day Silver Harbour programme.

signed:... date:...

to learn a bit more about this course and our company, please check our website. www.mellorquaid.co.nz

Thank you!

Target Market(s)

attendees who completed our 3 day programme.

Requirements
Must have
• Both our SH logo and our brand logo. a compass or a koru.
• a 25th year existence something on it.

```html
<!DOCTYPE html>
<html lang="en">
<head>
<meta charset="utf-8">
<title>Silver Harbour Certificate of Completion</title>
<link rel="stylesheet" href="https://fonts.googleapis.com/css2?family=Open+Sans:ital,wght@0,400;0,600;0,700;1,400;1,600&family=Great+Vibes&display=swap">
<style>
  :root {
    --backdrop: #333333;
    --paper: #ffffff;
    --green-dark: #6b9b2b;
    --green-light: #8dc63f;
    --green-text: #5ea02a;
    --ink: #1e1e1e;
    --brand-ink: #3a3a4a;
    --compass-tint: #e2eed0;
    --compass-ring: #c9dfa6;
    --seal-fill: #d3e6b5;
    --seal-ring: #8dc63f;
  }
  * { box-sizing: border-box; margin: 0; padding: 0; }
  html, body { width: 1200px; height: 1000px; overflow: hidden; }
  body {
    background: var(--backdrop);
    font-family: "Open Sans", Arial, sans-serif;
    position: relative;
  }
  .certificate {
    position: absolute;
    left: 80px; top: 120px;
    width: 1040px; height: 760px;
    background: var(--paper);
    overflow: hidden;
  }
  .certificate__art { position: absolute; inset: 0; }

  .compass-mark {
    position: absolute;
    left: 800px; top: -90px;
    width: 320px; height: 320px;
    border-radius: 50%;
    background: var(--compass-tint);
    border: 3px solid var(--compass-ring);
  }

  .brand-row {
    position: absolute;
    top: 196px; left: 150px; right: 170px;
    display: flex; justify-content: space-between; align-items: center;
  }
  .brand {
    display: flex; align-items: center; gap: 12px;
    font-weight: 600;
    color: var(--brand-ink);
    font-size: 21px;
  }
  .brand--company { letter-spacing: 0.5px; }
  .brand__square { width: 44px; height: 44px; background: var(--green-light); flex: none; }

  .certificate__title {
    position: absolute; top: 262px; left: 0; right: 0;
    text-align: center;
    font-family: "Great Vibes", cursive;
    font-weight: 400;
    font-size: 66px;
    color: var(--green-text);
  }
  .certificate__lead {
    position: absolute; top: 370px; left: 0; right: 0;
    text-align: center; font-style: italic; font-size: 19px; color: var(--ink);
  }
  .recipient {
    position: absolute; top: 418px; left: 50%;
    transform: translateX(-50%);
    width: 330px;
    text-align: center;
    font-weight: 700; font-size: 32px; color: var(--ink);
    padding-bottom: 6px;
    border-bottom: 3px solid var(--green-dark);
  }
  .certificate__reason {
    position: absolute; top: 496px; left: 0; right: 0;
    text-align: center; font-style: italic; font-size: 16px; line-height: 1.45; color: var(--ink);
  }
  .sign-field {
    position: absolute; top: 600px; width: 170px;
    border-top: 1.5px solid var(--green-light);
    text-align: center; padding-top: 6px;
    font-style: italic; font-weight: 600; font-size: 13px; color: var(--ink);
  }
  .sign-field--date { left: 230px; }
  .sign-field--signature { right: 230px; }

  .anniversary-seal {
    position: absolute; top: 570px; left: 50%;
    transform: translateX(-50%);
    width: 150px; height: 150px; border-radius: 50%;
    background: var(--seal-fill);
    border: 3px solid var(--seal-ring);
    box-shadow: 0 0 0 8px var(--paper);
  }
</style>
</head>
<body>
  <main class="certificate">
    <svg class="certificate__art" width="1040" height="760" viewBox="0 0 1040 760" aria-hidden="true">
      <polygon points="190,0 660,0 620,60 230,60" fill="var(--green-dark)"/>
      <g stroke="#ffffff" stroke-width="2.5">
        <polygon points="340,0 420,80 340,160 260,80" fill="var(--green-light)"/>
        <polygon points="500,0 580,80 500,160 420,80" fill="var(--green-light)"/>
        <line x1="340" y1="0" x2="340" y2="160"/><line x1="260" y1="80" x2="420" y2="80"/>
        <line x1="500" y1="0" x2="500" y2="160"/><line x1="420" y1="80" x2="580" y2="80"/>
      </g>
      <rect x="70" y="100" width="900" height="560" fill="none" stroke="var(--green-light)" stroke-width="2"/>
      <polygon points="0,470 0,760 230,760" fill="var(--green-dark)"/>
      <g stroke="#ffffff" stroke-width="2.5">
        <polygon points="80,580 165,665 80,750 -5,665" fill="var(--green-light)"/>
        <line x1="80" y1="580" x2="80" y2="750"/><line x1="-5" y1="665" x2="165" y2="665"/>
      </g>
      <polygon points="160,680 240,760 160,760" fill="var(--green-dark)"/>
      <polygon points="1040,450 1040,760 760,760" fill="var(--green-dark)"/>
      <g stroke="#ffffff" stroke-width="2.5">
        <polygon points="940,560 1030,650 940,740 850,650" fill="var(--green-light)"/>
        <line x1="940" y1="560" x2="940" y2="740"/><line x1="850" y1="650" x2="1030" y2="650"/>
      </g>
    </svg>

    <div class="compass-mark" role="img" aria-label="Compass rose decoration"></div>

    <div class="brand-row">
      <div class="brand brand--company"><span class="brand__square"></span>MELLOR QUAID &amp; Associates</div>
      <div class="brand brand--course"><span class="brand__square"></span>Silver Harbour</div>
    </div>

    <h1 class="certificate__title">Certificate of Completion</h1>
    <p class="certificate__lead">This certificate is awarded to</p>
    <p class="recipient">OLIVIA GRANT</p>
    <p class="certificate__reason">For successfully completing and contributing to the three day<br>Silver Harbour programme.</p>

    <div class="sign-field sign-field--date">Date</div>
    <div class="anniversary-seal" role="img" aria-label="Celebrating 25 years of existence anniversary seal"></div>
    <div class="sign-field sign-field--signature">Signature</div>
  </main>
</body>
</html>
```